New Business Card Design Project

Need a design that will create an impact / strong impression towards our clients for our business. We are in the lighting business and we do lighting retrofits for large commercial to industrial clientele.

Target Market(s)

Lighting Industry

Industry/Entity Type

Business

Font styles to use
Other font styles liked:
• we would like to use the font on our logo, not sure what it is though..

Requirements
Must have
• Our logo.
Nice to have
• We are open to suggestions that have to do with lighting.

```html
<!DOCTYPE html>
<html lang="en">
<head>
<meta charset="utf-8">
<title>Keystone Voltage Lighting – Business Card</title>
<link href="https://fonts.googleapis.com/css2?family=Montserrat:wght@300;400;500;700&display=swap" rel="stylesheet">
<style>
  :root {
    --page-bg: #d9dcd8;
    --card-bg: #eef0ee;
    --green-light: #2e7d3b;
    --green-dark: #0e4720;
    --strip: #1c2a21;
    --logo-green: #1f6b30;
    --ink-dark: #1d2620;
    --ink-light: #e9efe9;
    --ink-soft: #cfdccf;
  }
  * { margin: 0; padding: 0; box-sizing: border-box; }
  html, body {
    width: 1200px; height: 969px; overflow: hidden;
    background: var(--page-bg);
    font-family: "Montserrat", sans-serif;
  }
  .card {
    position: absolute; left: 100px; top: 200px;
    width: 1000px; height: 569px;
    background: var(--card-bg);
    box-shadow: 0 10px 30px rgba(0,0,0,.18);
    overflow: hidden;
  }
  .card__panel { position: absolute; inset: 0; width: 100%; height: 100%; }
  .card__strip {
    position: absolute; right: 0; top: 0;
    width: 30px; height: 100%; background: var(--strip);
  }
  .brand {
    position: absolute; left: 455px; top: 55px;
    display: flex; flex-direction: column; gap: 8px;
  }
  .brand__mark { display: flex; align-items: center; gap: 16px; }
  .brand__name {
    font-weight: 700; font-size: 96px; line-height: 1;
    color: var(--logo-green); letter-spacing: 2px;
  }
  .brand__square { width: 40px; height: 40px; background: var(--logo-green); }
  .brand__tagline {
    font-weight: 500; font-size: 19px; letter-spacing: 1px;
    color: var(--ink-dark); text-transform: uppercase;
  }
  .contact {
    position: absolute; left: 45px; top: 175px;
    color: var(--ink-light);
  }
  .contact__name { font-weight: 500; font-size: 31px; letter-spacing: 1px; line-height: 1.1; }
  .contact__role { font-weight: 300; font-size: 27px; letter-spacing: 1px; color: var(--ink-soft); margin-top: 2px; }
  .contact__address {
    font-style: normal; font-weight: 300; font-size: 26px;
    line-height: 33px; margin-top: 26px; color: var(--ink-soft);
  }
  .contact__list { list-style: none; margin-top: 22px; }
  .contact__item {
    display: flex; align-items: center; gap: 14px;
    font-weight: 300; font-size: 25px; line-height: 31.5px; color: var(--ink-soft);
  }
  .contact__icon { width: 18px; height: 18px; fill: var(--ink-soft); flex: none; }
</style>
</head>
<body>
  <main class="card">
    <svg class="card__panel" viewBox="0 0 1000 569" preserveAspectRatio="none" aria-hidden="true">
      <defs>
        <linearGradient id="panelGreen" x1="0" y1="0" x2="1" y2="1">
          <stop offset="0" stop-color="var(--green-light)"/>
          <stop offset="1" stop-color="var(--green-dark)"/>
        </linearGradient>
      </defs>
      <polygon points="0,0 232,0 629,569 0,569" fill="url(#panelGreen)"/>
    </svg>
    <div class="card__strip"></div>

    <div class="brand">
      <div class="brand__mark">
        <span class="brand__name">KVL</span>
        <span class="brand__square"></span>
      </div>
      <span class="brand__tagline">Keystone Voltage Lighting, LLC</span>
    </div>

    <section class="contact">
      <h1 class="contact__name">DANIEL REYES</h1>
      <p class="contact__role">CEO/FOUNDER</p>
      <address class="contact__address">
        2140 Cedarbrook Way<br>Fairbanks<br>Alaska 39816
      </address>
      <ul class="contact__list">
        <li class="contact__item">
          <svg class="contact__icon" viewBox="0 0 20 20"><path d="M2 6c0-2 2-3 8-3s8 1 8 3v2h-4V6H6v2H2z M4 9h12l2 8H2z"/></svg>
          512 309 7741
        </li>
        <li class="contact__item">
          <svg class="contact__icon" viewBox="0 0 20 20"><path d="M6 1h8a1 1 0 0 1 1 1v16a1 1 0 0 1-1 1H6a1 1 0 0 1-1-1V2a1 1 0 0 1 1-1zm1 2v12h6V3zm3 13a1 1 0 1 0 0 2 1 1 0 0 0 0-2z"/></svg>
          741 226 5083
        </li>
        <li class="contact__item">
          <svg class="contact__icon" viewBox="0 0 20 20"><path d="M5 2h10v5H5z M2 8h16v8h-3v2H5v-2H2z M7 13v3h6v-3z"/></svg>
          395 618 2270
        </li>
        <li class="contact__item">
          <svg class="contact__icon" viewBox="0 0 20 20"><path d="M2 5h16v10H2z M2 5l8 6 8-6" stroke="#0e4720" stroke-width="1.2"/></svg>
          contact@kvlighting.com
        </li>
        <li class="contact__item">
          <svg class="contact__icon" viewBox="0 0 20 20"><circle cx="10" cy="10" r="8"/><path d="M2 10h16M10 2c3 3 3 13 0 16M10 2c-3 3-3 13 0 16" stroke="#0e4720" stroke-width="1.2" fill="none"/></svg>
          www.kvlighting.com
        </li>
      </ul>
    </section>
  </main>
</body>
</html>
```